Flyer-Design für Kindertagesstätte
Felmriks Spielhafen suchte ein neues Design in der Kategorie Flyer und hat ein Projekt auf grafikwunsch.de gestartet.
Zielgruppe
Wir sind eine Kindertagesstätte und wollen eine Baby-Kind-Spielgruppe jeden Mittwoch in unserer Kita von 09.00 Uhr bis 11.00 Uhr anbieten.
Aufgabenstellung
Unser LOGO muss im Flyer enthalten sein, auf jeden Fall ein Bild wenn möglich mit mehreren Babys/Kleinkindern bis 1,5 Jahre. Wir benötigen den Flyer in DIN lang - bunt - 1 seitig.
Folgender Text sollte enthalten: Baby-Kind-Spielgruppe, jeden mittwoch in unserer Kita 'Felmriks Spielhafen' von 09.00 Uhr bis 11.00 Uhr. Die Spielgruppe wird durch unser ausgebildetes Fachpersonal begleitet.

```html
<!DOCTYPE html>
<html lang="de">
<head>
<meta charset="utf-8">
<title>Felmriks Spielhafen – Baby-Kind-Spielgruppe Flyer</title>
<link rel="stylesheet" href="https://fonts.googleapis.com/css2?family=Open+Sans:wght@400;600;700&family=Roboto+Slab:wght@600&display=swap">
<style>
  :root {
    --bg: #e6e6e6;
    --paper: #ffffff;
    --orange: #e2661f;
    --orange-soft: #f08a2a;
    --green: #8fbc1e;
    --brown: #6b2a1e;
    --ink: #2b2b2b;
    --body: #555555;
    --pink: #e0246f;
    --blue: #1d5fb8;
    --yellow: #f5c400;
    --cyan: #27b3d6;
  }
  * { margin: 0; padding: 0; box-sizing: border-box; }
  html, body { width: 1200px; height: 800px; overflow: hidden; background: var(--bg); }
  .canvas { position: relative; width: 1200px; height: 800px; }
  .flyer {
    position: absolute; left: 420px; top: 20px; width: 360px; height: 760px;
    background: var(--paper); overflow: hidden;
    box-shadow: 0 6px 18px rgba(0,0,0,0.18);
    font-family: "Open Sans", Arial, sans-serif;
  }
  .flyer__hero { position: absolute; left: 0; top: 0; }
  .schedule-badge { position: absolute; left: 8px; top: 262px; width: 176px; height: 176px; }
  .schedule-badge__text {
    position: absolute; inset: 0; display: flex; flex-direction: column;
    align-items: center; justify-content: center; color: #fff; text-align: center;
  }
  .schedule-badge__day { font-size: 28px; font-weight: 400; line-height: 1.1; }
  .schedule-badge__time { font-size: 14px; margin-top: 4px; }
  .brand {
    position: absolute; left: 222px; top: 318px; width: 128px;
    display: flex; flex-direction: column; align-items: center; gap: 8px;
  }
  .brand__dot { width: 26px; height: 26px; border-radius: 50%; background: var(--orange); }
  .brand__name {
    font-family: "Open Sans", Arial, sans-serif; font-weight: 700; font-size: 19px;
    line-height: 1.1; color: var(--brown); text-align: center;
  }
  .flyer__content { position: absolute; left: 26px; top: 470px; width: 230px; }
  .headline {
    font-family: "Roboto Slab", Georgia, serif; font-weight: 600; font-size: 22px;
    color: var(--orange); line-height: 1.15;
  }
  .subline { font-size: 15px; font-weight: 600; color: var(--ink); margin-top: 4px; }
  .body-copy { font-size: 8.5px; color: var(--body); line-height: 1.45; margin-top: 8px; }
  .body-copy strong { color: var(--ink); }
  .cta { position: absolute; left: 26px; top: 648px; }
  .cta__label { font-size: 13px; font-weight: 600; color: var(--orange); letter-spacing: 0.5px; }
  .cta__web { font-size: 12px; color: var(--orange); letter-spacing: 0.6px; }
  .flyer__illustration { position: absolute; right: 0; top: 560px; }
  .confetti { position: absolute; left: 0; top: 0; pointer-events: none; }
</style>
</head>
<body>
<main class="canvas">
  <article class="flyer">
    <svg class="flyer__hero" width="360" height="340" viewBox="0 0 360 340">
      <defs>
        <linearGradient id="heroTones" x1="0" y1="0" x2="1" y2="1">
          <stop offset="0" stop-color="#f3c7a8"/>
          <stop offset="0.35" stop-color="#f4b400"/>
          <stop offset="0.65" stop-color="#e8452a"/>
          <stop offset="1" stop-color="#e9a3b4"/>
        </linearGradient>
      </defs>
      <polygon points="300,0 360,0 360,50" fill="var(--blue)"/>
      <path d="M0,0 H262 A62,62 0 0 1 300,108 A76,76 0 0 1 262,240 A80,80 0 0 1 140,318 L0,318 Z"
            fill="none" stroke="var(--orange-soft)" stroke-width="18"/>
      <path d="M0,0 H262 A62,62 0 0 1 300,108 A76,76 0 0 1 262,240 A80,80 0 0 1 140,318 L0,318 Z"
            fill="url(#heroTones)" role="img" aria-label="Foto: mehrere lachende Babys liegen im Kreis auf einer bunten Decke"/>
    </svg>

    <div class="schedule-badge">
      <svg width="176" height="176" viewBox="0 0 176 176">
        <circle cx="88" cy="88" r="86" fill="var(--green)"/>
        <circle cx="88" cy="88" r="74" fill="none" stroke="#fff" stroke-width="2" stroke-dasharray="7 5"/>
      </svg>
      <div class="schedule-badge__text">
        <span class="schedule-badge__day">Mittwochs</span>
        <span class="schedule-badge__time">09.00 bis 11.00 Uhr</span>
      </div>
    </div>

    <div class="brand">
      <span class="brand__dot"></span>
      <span class="brand__name">Felmriks Spielhafen</span>
    </div>

    <section class="flyer__content">
      <h1 class="headline">Baby-Kind-Spielgruppe</h1>
      <p class="subline">Jeden Mittwoch in unserer Kita</p>
      <p class="body-copy">Die Spielgruppe wird durch unser ausgebildetes <strong>Fachpersonal</strong> begleitet.</p>
      <p class="body-copy">Voranmeldungen bitte unter telefonisch unter: <strong>0351-4820716</strong> oder unter <strong>www.felmriks-spielhafen.de</strong>. Spielgruppe ist öffentlich und kostenfrei.</p>
    </section>

    <div class="cta">
      <p class="cta__label">JETZT ANMELDEN</p>
      <p class="cta__web">www.felmriks-spielhafen.de</p>
    </div>

    <svg class="flyer__illustration" width="130" height="150" viewBox="0 0 130 150">
      <defs>
        <linearGradient id="toyTones" x1="0" y1="0" x2="1" y2="1">
          <stop offset="0" stop-color="#3a6fd0"/>
          <stop offset="0.5" stop-color="#f5c400"/>
          <stop offset="1" stop-color="#d84aa8"/>
        </linearGradient>
      </defs>
      <path d="M20,150 Q10,80 60,40 Q100,10 130,0 V150 Z" fill="url(#toyTones)" opacity="0.85"
            role="img" aria-label="Illustration: Rakete, kleiner Dinosaurier und bunte Spielsachen"/>
    </svg>

    <svg class="confetti" width="360" height="760" viewBox="0 0 360 760" aria-hidden="true">
      <polygon points="298,330 304,340 292,340" fill="var(--pink)"/>
      <circle cx="332" cy="345" r="5" fill="var(--cyan)"/>
      <circle cx="312" cy="480" r="8" fill="var(--green)"/>
      <circle cx="270" cy="500" r="5" fill="var(--pink)"/>
      <circle cx="320" cy="520" r="3" fill="var(--blue)"/>
      <circle cx="200" cy="720" r="6" fill="var(--pink)"/>
      <circle cx="150" cy="735" r="3" fill="var(--yellow)"/>
      <polygon points="100,725 106,733 94,733" fill="var(--blue)"/>
      <circle cx="60" cy="745" r="3" fill="var(--cyan)"/>
      <circle cx="245" cy="745" r="4" fill="var(--green)"/>
    </svg>
  </article>
</main>
</body>
</html>
```